Design Cover for Catalog and theme pages to match cover design for continuity

I need a catalog cover for our new catalog and have it flow through the pages uniting the design together. Most the hardest work is complete however it needs a designers touch to bring it all together. The attached files include the catalog with products images data and logos. We have more assets however with the 100MB limit we are unable to upload to many more. For additional images you can pull them from our website www.brovantek.example.

Target Market(s)

Tradesmen and trades women who work in the Electrical and Industrial Automation spaces.

Industry/Entity Type

Industrial

Font styles to use
Sans Serif

Colors
3176b5
0555a3
85cae6

Requirements
Must have
• Complete cover design
• Must also have cover theme flow through remaining pages
Nice to have
• Header and Footer on each page
• Index on cover with page reference
Should not have
• This is not a redesign of the whole catalog, please don't drastically change the pages or any of the data in the tables.

```html
<!DOCTYPE html>
<html lang="en">
<head>
<meta charset="utf-8">
<title>Products and Services Catalogue – Cover</title>
<link href="https://fonts.googleapis.com/css2?family=Oswald:wght@300;400;500;700&family=Barlow:wght@400;600&display=swap" rel="stylesheet">
<style>
  :root {
    --backdrop: #2f62a6;
    --paper: #ffffff;
    --ink-grey: #8a8a8a;
    --brand-blue: #3176b5;
    --deep-blue: #0555a3;
    --panel-blue: #4675b8;
    --panel-veil: rgba(38, 86, 160, 0.78);
    --white: #ffffff;
  }
  * { margin: 0; padding: 0; box-sizing: border-box; }
  html, body {
    width: 1200px;
    height: 1200px;
    overflow: hidden;
    background: var(--backdrop);
  }
  .canvas {
    position: relative;
    width: 1200px;
    height: 1200px;
  }
  .cover {
    position: absolute;
    left: 165px;
    top: 40px;
    width: 870px;
    height: 1120px;
    background: var(--paper);
    box-shadow: 0 6px 24px rgba(0, 0, 0, 0.25);
  }
  .cover-year {
    position: absolute;
    left: 36px;
    top: 38px;
    font-family: "Oswald", sans-serif;
    font-weight: 400;
    font-size: 42px;
    letter-spacing: -1px;
    color: var(--ink-grey);
    line-height: 1;
  }
  .cover-intro {
    position: absolute;
    left: 174px;
    top: 40px;
    width: 420px;
    font-family: "Barlow", sans-serif;
    font-size: 12px;
    line-height: 22px;
    color: var(--ink-grey);
  }
  .cover-photo {
    position: absolute;
    left: 39px;
    top: 110px;
    width: 792px;
    height: 855px;
    background:
      repeating-linear-gradient(-14deg, rgba(255,255,255,0.18) 0 22px, rgba(0,0,0,0.12) 22px 44px),
      linear-gradient(135deg, #b9b9b9 0%, #8c8c8c 45%, #a6a6a6 100%);
  }
  .title-panel {
    position: absolute;
    left: 76px;
    top: 632px;
    width: 417px;
    height: 333px;
    background: var(--panel-veil);
  }
  .title-main {
    position: absolute;
    left: 53px;
    top: 52px;
    font-family: "Oswald", sans-serif;
    font-weight: 700;
    font-size: 62px;
    line-height: 62px;
    letter-spacing: -1px;
    color: var(--white);
    text-transform: uppercase;
  }
  .title-sub {
    position: absolute;
    left: 53px;
    top: 192px;
    font-family: "Oswald", sans-serif;
    font-weight: 300;
    font-size: 32px;
    line-height: 1;
    color: #dbe6f4;
    text-transform: uppercase;
  }
  .slogan-panel {
    position: absolute;
    left: 76px;
    top: 965px;
    width: 417px;
    height: 116px;
    background: var(--panel-blue);
  }
  .slogan {
    position: absolute;
    left: 53px;
    top: 25px;
    font-family: "Oswald", sans-serif;
    font-weight: 400;
    font-size: 19px;
    line-height: 22px;
    letter-spacing: 2px;
    color: var(--white);
    text-transform: uppercase;
  }
  .brand {
    position: absolute;
    left: 580px;
    top: 1000px;
    display: flex;
    align-items: center;
    gap: 10px;
  }
  .brand-dot {
    width: 30px;
    height: 30px;
    border-radius: 50%;
    background: var(--brand-blue);
  }
  .brand-name {
    font-family: "Barlow", sans-serif;
    font-weight: 600;
    font-size: 36px;
    line-height: 1;
    color: var(--brand-blue);
  }
</style>
</head>
<body>
  <main class="canvas">
    <article class="cover">
      <div class="cover-year">2017</div>
      <p class="cover-intro">Our products and services are developed to maximize<br>productivity with minimum waste of time and effort.</p>

      <div class="cover-photo" role="img" aria-label="Black and white photograph of rows of metal terminal strips with screws, arranged diagonally"></div>

      <section class="title-panel">
        <h1 class="title-main">Products<br>and Services</h1>
        <div class="title-sub">Catalogue</div>
      </section>

      <section class="slogan-panel">
        <p class="slogan">Efficiency<br>through<br>simplicity.</p>
      </section>

      <div class="brand">
        <span class="brand-dot"></span>
        <span class="brand-name">Brovantek</span>
      </div>
    </article>
  </main>
</body>
</html>
```